BuildLinkHub.com Full Stationery Design

Business Card will have all info on it. Letterhead will not have name, title or mobile number. Keep general feeling very clean, using colors from the logo as accents.
Name:Dale Marchetti
Title:President
Phone: 1-800-555-0142
Cell: 306-555-0187
email: dale@buildlinkhub.example
website: www.buildlinkhub.example
Address:
PO Box 947
Ridgeford, MB
S0J2T0

Target Market(s)

Construction Business owners

Industry/Entity Type

Business

Contact Information for Business Card

Name:Dale Marchetti
Title:President
Phone: 1-800-555-0142
Cell: 306-555-0187
Address:
PO Box 947
Ridgeford, MB
S0J2T0

Font styles to use
Sans Serif

Requirements
Must have
• Clean look
Should not have
• Images or cartoon type characters or tools

```html
<!DOCTYPE html>
<html lang="en">
<head>
<meta charset="utf-8">
<title>BuildLinkHub.com Business Card</title>
<link href="https://fonts.googleapis.com/css2?family=Mulish:wght@400;600;700&display=swap" rel="stylesheet">
<style>
  :root {
    --backdrop: #5b4a3c;
    --slate-dark: #4a5a6b;
    --slate-light: #687e90;
    --brand-orange: #f07a22;
    --ink-slate: #3f4e5e;
    --ink-grey: #4a4a4a;
    --paper: #ffffff;
  }
  * { margin: 0; padding: 0; box-sizing: border-box; }
  html, body {
    width: 1200px; height: 987px; overflow: hidden;
    background: var(--backdrop);
    font-family: "Mulish", sans-serif;
  }
  .canvas { position: relative; width: 1200px; height: 987px; }
  .card {
    position: absolute; left: 293px; width: 615px; height: 351px;
    overflow: hidden; background: var(--paper);
    box-shadow: 0 2px 6px rgba(0,0,0,0.35);
  }
  .card--front { top: 130px; background: linear-gradient(160deg, var(--slate-dark) 0%, var(--slate-light) 100%); }
  .card--back { top: 505px; }

  .front-band { position: absolute; inset: 0; }

  .holder { position: absolute; left: 37px; top: 34px; }
  .holder__name { color: var(--brand-orange); font-weight: 700; font-size: 21px; line-height: 1.2; }
  .holder__title { color: #fff; font-size: 16px; line-height: 1.2; margin-top: 2px; }

  .address { position: absolute; left: 37px; top: 175px; color: #fff; font-size: 15px; line-height: 20px; }

  .contact-list { position: absolute; left: 37px; top: 226px; list-style: none; color: #fff; font-size: 15px; }
  .contact-list li { display: flex; align-items: center; height: 23px; }
  .contact-list svg { width: 14px; height: 14px; margin-right: 8px; fill: var(--brand-orange); flex: none; }

  .brand { position: absolute; left: 0; right: 0; top: 150px; display: flex; justify-content: center; align-items: center; gap: 14px; }
  .brand__square { width: 30px; height: 30px; background: var(--brand-orange); }
  .brand__name { color: var(--ink-slate); font-weight: 700; font-size: 32px; letter-spacing: 0.3px; }

  .back-web { position: absolute; left: 0; right: 0; top: 292px; text-align: center; color: var(--ink-grey); font-size: 16px; }
</style>
</head>
<body>
<main class="canvas">
  <section class="card card--front">
    <svg class="front-band" viewBox="0 0 615 351" width="615" height="351" aria-hidden="true">
      <polygon points="422,0 615,0 615,351 456,351 304,257 304,87" fill="var(--paper)"/>
      <polyline points="422,0 304,87 304,257 456,351" fill="none" stroke="var(--paper)" stroke-width="5"/>
    </svg>
    <div class="holder">
      <p class="holder__name">Dale Marchetti</p>
      <p class="holder__title">President</p>
    </div>
    <p class="address">PO Box 947<br>Ridgeford, MB, S0J2T0</p>
    <ul class="contact-list">
      <li><svg viewBox="0 0 24 24"><path d="M6.6 10.8a15.1 15.1 0 0 0 6.6 6.6l2.2-2.2c.3-.3.7-.4 1-.2 1.1.4 2.3.6 3.6.6.6 0 1 .4 1 1V20c0 .6-.4 1-1 1A17 17 0 0 1 3 4c0-.6.4-1 1-1h3.5c.6 0 1 .4 1 1 0 1.3.2 2.5.6 3.6.1.3 0 .7-.2 1z"/></svg>1-800-555-0142</li>
      <li><svg viewBox="0 0 24 24"><path d="M7 1h10a2 2 0 0 1 2 2v18a2 2 0 0 1-2 2H7a2 2 0 0 1-2-2V3a2 2 0 0 1 2-2zm0 3v14h10V4zm5 15.5a1.2 1.2 0 1 0 0 2.4 1.2 1.2 0 0 0 0-2.4z"/></svg>306-555-0187</li>
      <li><svg viewBox="0 0 24 24"><path d="M2 5h20v14H2zm2 2v.5l8 5 8-5V7zm0 2.8V17h16V9.8l-8 5z"/></svg>dale@buildlinkhub.example</li>
      <li><svg viewBox="0 0 24 24"><path d="M12 2a10 10 0 1 0 0 20 10 10 0 0 0 0-20zm-1 17.9A8 8 0 0 1 4.2 10.2L9 15v1a2 2 0 0 0 2 2zm6.9-2.5A2 2 0 0 0 16 16h-1v-3a1 1 0 0 0-1-1H8v-2h2a1 1 0 0 0 1-1V7h2a2 2 0 0 0 2-2v-.4a8 8 0 0 1 2.9 12.8z"/></svg>www.buildlinkhub.example</li>
    </ul>
  </section>

  <section class="card card--back">
    <div class="brand">
      <span class="brand__square" aria-hidden="true"></span>
      <span class="brand__name">BuildLinkHub.com</span>
    </div>
    <p class="back-web">www.buildlinkhub.example</p>
  </section>
</main>
</body>
</html>
```